Flyer for Tallow Brisko - Design Agency

We need a 4-page square flyer measuring 14.8x14.8cm per page, to fold out, for a design agency targeting small businesses.
The design should be very modern. There shouldn't be too much content visible.
The background should be black. The color of the logo (attached) can also be used. The content is also attached and divided per page. We are open to alternative suggestions regarding the division.

```html
<!DOCTYPE html>
<html lang="de">
<head>
<meta charset="utf-8">
<title>Tallow Brisko – Faltflyer</title>
<link rel="stylesheet" href="https://fonts.googleapis.com/css2?family=Poppins:wght@300;400;500;600;700&family=Lexend:wght@400;600&display=swap">
<style>
  :root {
    --ink: #000000;
    --paper: #eeeeee;
    --teal: #8fd6d8;
    --teal-deep: #3e8f97;
    --teal-soft: rgba(143, 214, 216, 0.28);
    --white: #ffffff;
  }
  * { box-sizing: border-box; margin: 0; padding: 0; }
  html, body { width: 745px; height: 1200px; overflow: hidden; background: var(--paper); }
  body { position: relative; font-family: "Poppins", sans-serif; color: var(--white); }

  .spread { position: absolute; left: 20px; width: 705px; height: 352px; background: var(--ink); overflow: hidden; }
  .spread--outside { top: 238px; }
  .spread--inside { top: 610px; }
  .abs { position: absolute; }
  .center { transform: translateX(-50%); text-align: center; white-space: nowrap; }

  /* ornament areas: flat tone only */
  .ornament { position: absolute; background: var(--teal-soft); border-radius: 2px; }
  .wave-area { position: absolute; }
  .wave-area--bottom { background: linear-gradient(90deg, rgba(62,143,151,0.05) 0%, rgba(62,143,151,0.45) 55%, rgba(62,143,151,0.1) 100%); }
  .wave-area--top { background: linear-gradient(90deg, rgba(62,143,151,0) 0%, rgba(62,143,151,0.5) 60%, rgba(143,214,216,0.2) 100%); }

  .deco-circle { position: absolute; border: 1.3px solid var(--teal); border-radius: 50%; }
  .deco-x { position: absolute; font: 400 12px/1 "Poppins", sans-serif; color: var(--teal); }
  .deco-x--white { color: var(--white); font-size: 8px; }

  .brand-name { font-family: "Poppins", sans-serif; font-weight: 600; color: var(--teal); line-height: 1; }

  /* outside: back cover */
  .back-logo { left: 177px; top: 38px; font-size: 26px; }
  .claim { left: 177px; top: 92px; font-size: 14px; font-weight: 600; line-height: 20.5px; }
  .cta { left: 31px; top: 148px; width: 292px; height: 21px; border: 1.2px solid var(--teal); border-radius: 11px;
    color: var(--teal); font-size: 11px; line-height: 19px; text-align: center; white-space: nowrap; }
  .contact { left: 177px; font-size: 10px; line-height: 12px; display: flex; align-items: center; gap: 4px; }
  .contact svg { width: 10px; height: 10px; }
  .owners { left: 177px; top: 268px; font-size: 10px; line-height: 12px; }
  .owners span { color: var(--teal); }

  /* outside: front cover */
  .cover-photo { left: 353px; top: 0; width: 352px; height: 216px;
    background: radial-gradient(circle at 82% 22%, #3a3a3a 0%, #1d1d1d 38%, #0b0b0b 80%); }
  .front-logo { left: 529px; top: 96px; font-size: 38px; }
  .tagline { left: 529px; font-family: "Lexend", sans-serif; letter-spacing: 1.6px; line-height: 1; font-size: 22px; }
  .tagline--soft { color: var(--teal); font-weight: 400; }
  .tagline--strong { color: var(--white); font-weight: 600; }

  /* inside: intro page */
  .intro-title { left: 37px; top: 31px; font-size: 15.5px; font-weight: 600; line-height: 20.5px; }
  .intro-title .brand-name { font-size: 15.5px; line-height: 20.5px; }
  .intro-text { left: 37px; top: 102px; font-size: 12px; font-weight: 300; line-height: 17.3px; white-space: nowrap; }
  .idea-art { left: 60px; top: 208px; width: 116px; height: 124px;
    background: radial-gradient(ellipse at 50% 45%, rgba(143,214,216,0.3) 0%, rgba(62,143,151,0.12) 50%, rgba(0,0,0,0) 78%); }

  /* inside: services page */
  .section-title { left: 367px; font-size: 15px; font-weight: 600; color: var(--teal); line-height: 1; }
  .service { left: 383px; display: flex; gap: 9px; white-space: nowrap; }
  .service-icon { flex: none; width: 27px; height: 31px; border: 1.1px solid var(--white); border-radius: 3px;
    display: flex; align-items: center; justify-content: center; }
  .service-icon svg { width: 16px; height: 16px; }
  .service-name { font-size: 9.5px; font-weight: 600; color: var(--teal); line-height: 12px; }
  .service-text { font-size: 9px; font-weight: 300; line-height: 11px; }
  .reasons { left: 387px; top: 265px; list-style: none; white-space: nowrap; }
  .reasons li { position: relative; padding-left: 16px; font-size: 8.6px; font-weight: 300; line-height: 13px; }
  .reasons li::before { content: ""; position: absolute; left: 0; top: 3px; width: 7px; height: 7px;
    border: 1px solid var(--white); border-radius: 50%; }
</style>
</head>
<body>

<section class="spread spread--outside" aria-label="Außenseite: Rückseite und Titelseite">
  <div class="wave-area wave-area--bottom" style="left:0;top:295px;width:355px;height:57px;" role="img" aria-label="Fließende türkise Wellenform am unteren Rand"></div>

  <div class="ornament" style="left:20px;top:33px;width:18px;height:16px;" role="img" aria-label="Punktraster-Ornament"></div>
  <div class="deco-circle" style="left:284px;top:22px;width:28px;height:28px;"></div>
  <div class="ornament" style="left:40px;top:82px;width:41px;height:12px;" role="img" aria-label="Zickzack-Ornament"></div>
  <div class="deco-x" style="left:328px;top:97px;">X</div>

  <div class="abs center brand-name back-logo">Tallow Brisko</div>
  <h2 class="abs center claim">Designs, die wirken.<br>Marken, die bleiben.</h2>
  <div class="abs cta">Kontaktiere uns für eine kostenlose Beratung!</div>
  <div class="abs center contact" style="top:189px;">
    <svg viewBox="0 0 16 16" aria-hidden="true"><rect x="1" y="3" width="14" height="10" fill="#fff"/><path d="M1 3l7 6 7-6" fill="none" stroke="#000" stroke-width="1.3"/></svg>
    design@tallowbrisko.de
  </div>
  <div class="abs center contact" style="top:208px;">
    <svg viewBox="0 0 16 16" aria-hidden="true"><path d="M4 1l3 3-2 2c1 2 3 4 5 5l2-2 3 3-2 3C7 15 1 9 1 3z" fill="none" stroke="#fff" stroke-width="1.5"/></svg>
    +49 123 98210
  </div>
  <div class="abs center contact" style="top:226px;">
    <svg viewBox="0 0 16 16" aria-hidden="true"><path d="M8 15S3 9 3 6a5 5 0 0 1 10 0c0 3-5 9-5 9z" fill="#fff"/><circle cx="8" cy="6" r="1.8" fill="#000"/></svg>
    Lindenweg 8, 60311 Frankfurt
  </div>
  <p class="abs center owners"><span>Inhaber:</span> Jona Fels &amp; Mira Stadler</p>

  <div class="abs cover-photo" role="img" aria-label="Dunkles Foto eines Schreibtischs mit Kaffeetasse, Stift und Designmaterialien"></div>
  <div class="ornament" style="left:568px;top:27px;width:40px;height:13px;" role="img" aria-label="Zickzack-Ornament"></div>
  <div class="ornament" style="left:387px;top:131px;width:6px;height:24px;" role="img" aria-label="Punktraster-Ornament"></div>
  <div class="deco-circle" style="left:655px;top:118px;width:19px;height:19px;"></div>
  <div class="deco-x deco-x--white" style="left:686px;top:170px;">X</div>
  <div class="abs center brand-name front-logo">Tallow Brisko</div>
  <p class="abs center tagline tagline--soft" style="top:220px;">Dein Unternehmen</p>
  <p class="abs center tagline tagline--soft" style="top:246px;">Dein Stil</p>
  <p class="abs center tagline tagline--strong" style="top:275px;">Unser Design</p>
  <div class="deco-x" style="left:660px;top:268px;">X</div>
  <div class="deco-circle" style="left:394px;top:323px;width:11px;height:11px;"></div>
  <div class="ornament" style="left:669px;top:324px;width:12px;height:12px;" role="img" aria-label="Punktraster-Ornament"></div>
</section>

<section class="spread spread--inside" aria-label="Innenseite: Vorstellung und Leistungen">
  <div class="wave-area wave-area--top" style="left:515px;top:0;width:190px;height:52px;" role="img" aria-label="Fließende türkise Wellenform oben rechts"></div>
  <div class="wave-area wave-area--bottom" style="left:0;top:295px;width:355px;height:57px;" role="img" aria-label="Fließende türkise Wellenform am unteren Rand"></div>

  <h2 class="abs intro-title"><span class="brand-name">Tallow Brisko</span><br>gestaltet die Zukunft deines<br>Unternehmensauftritts.</h2>
  <p class="abs intro-text">Wir machen aus Ideen visuelle Erlebnisse<br>und sorgen dafür, dass deine Marke im<br>Gedächtnis bleibt.</p>
  <div class="ornament" style="left:277px;top:29px;width:40px;height:12px;" role="img" aria-label="Zickzack-Ornament"></div>
  <div class="ornament" style="left:27px;top:186px;width:26px;height:6px;" role="img" aria-label="Punktraster-Ornament"></div>
  <div class="deco-x deco-x--white" style="left:279px;top:183px;">X</div>
  <div class="deco-circle" style="left:270px;top:230px;width:19px;height:19px;"></div>
  <div class="abs idea-art" role="img" aria-label="Illustration einer leuchtenden Glühbirne als Symbol für Ideen"></div>

  <h2 class="abs section-title" style="top:33px;">Unsere Leistungen:</h2>

  <div class="abs service" style="top:60px;">
    <div class="service-icon"><svg viewBox="0 0 16 16" aria-hidden="true"><path d="M8 2l6 6H2z M4 8v6h8V8" fill="none" stroke="#fff" stroke-width="1.2"/></svg></div>
    <div><p class="service-name">Next-Level Flyer</p><p class="service-text">Nicht nur Papier, sondern deine Botschaft<br>im perfekten Look.</p></div>
  </div>
  <div class="abs service" style="top:105px;">
    <div class="service-icon"><svg viewBox="0 0 16 16" aria-hidden="true"><circle cx="8" cy="8" r="6" fill="none" stroke="#fff" stroke-width="1.2"/><circle cx="6" cy="6" r="1" fill="#fff"/><circle cx="10" cy="6" r="1" fill="#fff"/><circle cx="6" cy="10" r="1" fill="#fff"/></svg></div>
    <div><p class="service-name">Corporate Identity</p><p class="service-text">Ein Design, das deine Marke spricht –<br>individuell, stark, unvergesslich.</p></div>
  </div>
  <div class="abs service" style="top:151px;">
    <div class="service-icon"><svg viewBox="0 0 16 16" aria-hidden="true"><circle cx="8" cy="8" r="6" fill="none" stroke="#fff" stroke-width="1.2"/><path d="M2 8h12M8 2c3 3 3 9 0 12M8 2c-3 3-3 9 0 12" fill="none" stroke="#fff" stroke-width="1"/></svg></div>
    <div><p class="service-name">Digital &amp; Print</p><p class="service-text">Ob Social Media Grafiken oder klassisches<br>Printdesign – wir sind da, wo du uns brauchst.</p></div>
  </div>
  <div class="abs service" style="top:198px;">
    <div class="service-icon"><svg viewBox="0 0 16 16" aria-hidden="true"><path d="M8 1l2 5 5 2-5 2-2 5-2-5-5-2 5-2z" fill="none" stroke="#fff" stroke-width="1.2"/></svg></div>
    <div><p class="service-name">Alles aus einer Hand</p><p class="service-text">Logo, Farben, Typografie, Flyer und vieles mehr –<br>wir bauen das Fundament für deinen Erfolg.</p></div>
  </div>
  <div class="ornament" style="left:626px;top:114px;width:40px;height:12px;" role="img" aria-label="Zickzack-Ornament"></div>
  <div class="deco-circle" style="left:675px;top:231px;width:18px;height:18px;"></div>

  <h2 class="abs section-title" style="top:244px;">Warum wir?</h2>
  <ul class="abs reasons">
    <li>Dein Style, unser Know-how: Wir kombinieren deine Vision mit<br>moderner Ästhetik.</li>
    <li>Persönlicher Service – Wir hören zu und setzen um, was dich<br>einzigartig macht</li>
    <li>Flexible Lösungen für die unterschiedlichsten Anforderungen</li>
  </ul>
</section>

</body>
</html>
```